Flyer-Design für persönlichen Lauftrainer
Zielgruppe
Die Trabwerk GmbH entwickelt und vertreibt den persönlichen Lauftrainer KOBAL. KOBAL ist ein elektrisch angetriebenes, automatisch gesteuertes Fahrzeug, mithilfe dessen eine Person ein professionell geplantes Lauftraining im Freien absolvieren kann. Das Gerät übernimmt die Trainingssteuerung und fungiert dabei quasi als ein persönlicher Lauftrainer.
Wir sprechen zwei Kundengruppen an:
1. Privatkunden
2. Institutionelle Kunden wie Physiotherapiezentren und -praxen, Sport- und Wellnesshotels, betriebliches Gesundheitsmanagement und Verleihgeschäfte.
Die Gestaltung, Funktionalität und Ausstattung des Geräts spricht jedoch grundsätzlich die Gesamtheit der Läufer und Fun- und Aktivsportler an.
Aufgabenstellung
Für unseren Produktflyer der DINA 4 und beidseitig bedruckt sein soll, suchen wir nach einem sportlichen, kräftigen, dynamischen Design. Das Design sollte für uns im Nachhinein leicht veränderbar sein (Texte, Bilder, etc.), da wir den Flyer für verschiedene geographische Regionen anpassen werden. Hierfür würden wir z.B. Indesign nutzen. Die Texte, die wir Ihnen mitliefern sollten möglichst so übernommen werden. Wenn Sie die Möglichkeit sehen, den Inhalt in anderer Form darzustellen, dann ist das in Ordnung.
Der Text für den Flyer ist folgender:
Slogan zum großen Bild: Sie brauchen einen persönlichen Lauftrainer?
Zu den kleinen Bildern: Schalten Sie KOBAL ein, wählen Sie ihr Trainingsprogramm und es kann los gehen!
Call to Action: Besuchen Sie www.trabwerk-beispiel.com
Adresse:
Trabwerk GmbH
www.trabwerk-beispiel.com
Text für Flyer:
Ihr Problem
⁃ Sie haben einen vollen Arbeitstag und wollen trotzdem endlich Ihre Fitness verbessern?
⁃ Sie möchten dringend an Ihrer Figur und Ihrem Gewicht arbeiten?
⁃ Sie wollen schon lange an Ihrem ersten 10 Kilometerlauf teilnehmen und sich optimal darauf vorbereiten?
⁃ Sie möchten einen Trainer haben, der Ihnen jederzeit zur Verfügung steht?
⁃ Mit Ihrer Pulsuhr und Ihrer Lauf-App machen Sie nur geringe oder gar keine Trainingsfortschritte?
Unsere Lösung KOBAL Ihr persönlicher Lauftrainer
⁃ bietet Ihnen ein optimales Lauftraining im Freien durch eine kontrollierte, direkte Geschwindigkeitsvorgabe,
⁃ alarmiert Sie nicht nur wenn Sie etwas falsch machen (indirektes Feedback), er zeigt Ihnen wie Sie es richtig machen (direktes Feedback),
⁃ führt dabei Trainingsprogramme aus, die auf Ihre individuellen Fitness- und Leistungsziele zugeschnitten sind,
⁃ verhindert, dass Sie sich beim Training überlasten,
⁃ unterstützt Sie als
⁃ Anfänger beim Trainingseinstieg
⁃ Fortgeschrittene beim Aufba..

```html
<!DOCTYPE html>
<html lang="de">
<head>
<meta charset="utf-8">
<title>KOBAL – Flyer</title>
<link href="https://fonts.googleapis.com/css2?family=Saira+Extra+Condensed:wght@500;700&family=Zilla+Slab:ital,wght@0,400;0,600;0,700;1,400;1,600&display=swap" rel="stylesheet">
<style>
  :root{
    --stage:#3b4046;
    --red:#e3202a;
    --pink:#f48b95;
    --yellow:#f2df1b;
    --navy:#2c3346;
    --violet:#57536f;
    --ink:#333;
    --white:#fff;
    --display:"Saira Extra Condensed", "Arial Narrow", sans-serif;
    --serif:"Zilla Slab", Georgia, serif;
  }
  *{box-sizing:border-box;margin:0;padding:0}
  html,body{width:1200px;height:831px;overflow:hidden;background:var(--stage)}
  .page{position:absolute;top:17px;width:565px;height:797px;overflow:hidden;background:var(--white);font-family:var(--serif)}
  .page--front{left:25px}
  .page--back{left:610px}
  .page__art{position:absolute;inset:0;width:565px;height:797px}
  .abs{position:absolute}
  .display{font-family:var(--display);font-weight:700}

  /* front */
  .cta{left:39px;top:646px}
  .brand{right:36px;top:724px;display:flex;align-items:center;gap:9px}
  .brand__dot{width:40px;height:40px;border-radius:50%;background:var(--red)}
  .brand__name{font-family:var(--display);font-weight:700;font-size:38px;line-height:1;color:var(--navy)}

  /* back */
  .bullets{list-style:none;color:var(--white);font-size:8.6px;line-height:11.3px}
  .bullets li{position:relative;padding-left:14px;margin-bottom:4px}
  .bullets li::before{content:"";position:absolute;left:2px;top:4.5px;width:3px;height:3px;border-radius:50%;background:var(--white)}
  .bullets em{font-weight:600}
  .bullets--problem{left:36px;top:79px;width:262px}
  .bullets--solution{left:36px;top:280px;width:290px}
  .availability{left:36px;top:395px;width:305px;color:var(--yellow)}
  .availability__title{font-family:var(--display);font-weight:700;font-size:9px;letter-spacing:.3px}
  .availability__text{font-size:9px;line-height:12px}
  .howto{right:14px;top:557px;width:258px;text-align:right;font-size:7.2px;line-height:10.4px;color:#444;list-style:none}
  .howto li{margin-bottom:2px}
  .contact{top:752px;font-size:7px;line-height:9px;font-weight:700;color:var(--navy);font-style:normal}
  .contact--address{left:282px}
  .contact--phone{left:364px;top:761px}
  .contact--web{left:461px;top:761px}
  .contact__key{color:var(--red)}
</style>
</head>
<body>

<section class="page page--front" aria-label="Flyer Vorderseite">
  <svg class="page__art" viewBox="0 0 748 1055">
    <defs>
      <linearGradient id="heroBlush" x1="0.25" y1="0.8" x2="1" y2="0">
        <stop offset="0" stop-color="#fff"/>
        <stop offset="0.55" stop-color="#fbd6da"/>
        <stop offset="1" stop-color="#f48b95"/>
      </linearGradient>
      <linearGradient id="heroScene" x1="0" y1="0" x2="0" y2="1">
        <stop offset="0.15" stop-color="#b9c8d6"/>
        <stop offset="0.45" stop-color="#c8bcc4"/>
        <stop offset="0.6" stop-color="#7c8456"/>
        <stop offset="0.75" stop-color="#8d8a86"/>
        <stop offset="1" stop-color="#9c9894"/>
      </linearGradient>
      <linearGradient id="footFade" x1="0" y1="0" x2="1" y2="0">
        <stop offset="0" stop-color="#fff" stop-opacity="0.95"/>
        <stop offset="0.6" stop-color="#fff" stop-opacity="0.85"/>
        <stop offset="1" stop-color="#fff"/>
      </linearGradient>
    </defs>
    <polygon points="0,0 748,0 748,176 251,297 0,230" fill="url(#heroBlush)"/>
    <polygon role="img" aria-label="Foto: älterer Läufer in grüner Kapuzenjacke stützt sich nach dem Lauf auf die Knie, Weg im Abendlicht" points="0,230 251,297 748,176 748,1055 0,1055" fill="url(#heroScene)"/>
    <polyline points="0,230 251,297 748,176" fill="none" stroke="#e3202a" stroke-width="6"/>
    <polygon points="0,815 130,785 480,875 748,810 748,1055 0,1055" fill="url(#footFade)"/>
    <line x1="480" y1="875" x2="748" y2="810" stroke="#e3202a" stroke-width="5"/>

    <text class="kicker" x="113" y="84" font-family="Zilla Slab, Georgia, serif" font-size="21" fill="#333" textLength="260" lengthAdjust="spacingAndGlyphs">SIE BRAUCHEN EINEN</text>
    <text class="headline" font-family="Saira Extra Condensed, Arial Narrow, sans-serif" font-weight="700" font-size="62" fill="#e3202a">
      <tspan x="113" y="150" textLength="306" lengthAdjust="spacingAndGlyphs">PERSÖNLICHEN</tspan>
      <tspan x="113" y="198" textLength="308" lengthAdjust="spacingAndGlyphs">LAUFTRAINER?</tspan>
    </text>
    <text class="cta__label" x="53" y="876" font-family="Saira Extra Condensed, Arial Narrow, sans-serif" font-weight="700" font-size="26" fill="#e3202a" textLength="135" lengthAdjust="spacingAndGlyphs">BESUCHEN SIE</text>
    <text class="cta__url" x="53" y="903" font-family="Zilla Slab, Georgia, serif" font-size="21" fill="#333" textLength="312" lengthAdjust="spacingAndGlyphs">WWW.TRABWERK-BEISPIEL.COM</text>
  </svg>

  <div class="abs brand">
    <span class="brand__dot"></span>
    <span class="brand__name">trabwerk</span>
  </div>
</section>

<section class="page page--back" aria-label="Flyer Rückseite">
  <svg class="page__art" viewBox="0 0 748 1055">
    <defs>
      <linearGradient id="runScene" x1="0" y1="0" x2="1" y2="0.3">
        <stop offset="0" stop-color="#8e8898"/>
        <stop offset="0.5" stop-color="#b0a5ab"/>
        <stop offset="1" stop-color="#d8cbc3"/>
      </linearGradient>
      <linearGradient id="road" x1="0" y1="0" x2="0" y2="1">
        <stop offset="0" stop-color="#8b8a8e" stop-opacity="0"/>
        <stop offset="1" stop-color="#6f6e72"/>
      </linearGradient>
      <linearGradient id="violetBar" x1="0" y1="0" x2="1" y2="0">
        <stop offset="0" stop-color="#3e3b59"/>
        <stop offset="1" stop-color="#8a86a3"/>
      </linearGradient>
      <path id="badgeArc" d="M 515 153 A 103 103 0 0 1 691 122"/>
    </defs>
    <rect role="img" aria-label="Foto: Läuferin folgt auf einem Weg dem gelben Lauftrainer-Fahrzeug im Gegenlicht" width="748" height="700" fill="url(#runScene)"/>
    <rect y="450" width="748" height="250" fill="url(#road)"/>

    <polygon points="0,590 440,590 487,688 748,688 748,1055 0,1055" fill="#fff"/>
    <polygon role="img" aria-label="Foto: Frau in rosa Jacke klappt den gelben Lauftrainer auf" points="0,608 210,608 258,718 210,833 0,833" fill="#c9b9a4"/>
    <polygon role="img" aria-label="Foto: Frau richtet die Lenkstange des gelben Lauftrainers auf" points="222,608 428,608 476,690 420,833 215,833 268,718" fill="#cdbfa6"/>
    <polygon role="img" aria-label="Foto: Läuferin startet hinter dem gelben Lauftrainer auf einem Parkweg" points="0,850 410,850 300,1055 0,1055" fill="#8e9b78"/>

    <polygon points="0,40 230,40 205,85 0,85" fill="#f2df1b"/>
    <polygon points="0,295 230,295 205,340 0,340" fill="#f2df1b"/>
    <polygon points="30,336 362,336 354,358 30,358" fill="url(#violetBar)"/>
    <polygon points="500,697 748,697 748,720 492,720" fill="url(#violetBar)"/>
    <line x1="382" y1="963" x2="748" y2="963" stroke="#555" stroke-width="1.5"/>

    <g font-family="Saira Extra Condensed, Arial Narrow, sans-serif" font-weight="700" fill="#fff">
      <text class="tag" x="48" y="74" font-size="26" textLength="125" lengthAdjust="spacingAndGlyphs">IHR PROBLEM</text>
      <text class="tag" x="48" y="328" font-size="26" textLength="153" lengthAdjust="spacingAndGlyphs">UNSERE LÖSUNG</text>
      <text class="howto-title" x="516" y="714" font-size="13" font-weight="500" textLength="142" lengthAdjust="spacingAndGlyphs">UND SO FUNKTIONIERT KOBAL</text>
    </g>
    <text class="subbar" x="48" y="352" font-family="Zilla Slab, Georgia, serif" font-weight="700" font-size="13" fill="#fff" textLength="246" lengthAdjust="spacingAndGlyphs">KOBAL – Ihr persönlicher Lauftrainer</text>

    <g class="badge">
      <circle cx="612" cy="188" r="96" fill="none" stroke="#f2df1b" stroke-width="2"/>
      <circle cx="612" cy="188" r="86" fill="#fff" fill-opacity="0.95"/>
      <text font-family="Saira Extra Condensed, Arial Narrow, sans-serif" font-weight="700" font-size="14" fill="#f2df1b">
        <textPath href="#badgeArc" textLength="200" lengthAdjust="spacingAndGlyphs">KOBAL UNTERSTÜTZT SIE ALS</textPath>
      </text>
      <g font-family="Saira Extra Condensed, Arial Narrow, sans-serif" font-weight="500" font-size="12" fill="#2c3346" text-anchor="middle" transform="rotate(-5 612 188)">
        <text x="612" y="142" textLength="80" lengthAdjust="spacingAndGlyphs">ANFÄNGER BEIM</text>
        <text x="612" y="155" textLength="98" lengthAdjust="spacingAndGlyphs">TRAININGSEINSTIEG</text>
        <text x="612" y="181" textLength="126" lengthAdjust="spacingAndGlyphs">FORTGESCHRITTENE BEIM</text>
        <text x="612" y="194" textLength="86" lengthAdjust="spacingAndGlyphs">AUFBAUTRAINING</text>
        <text x="612" y="220" textLength="90" lengthAdjust="spacingAndGlyphs">"PROFI" BEI EINER</text>
        <text x="612" y="233" textLength="116" lengthAdjust="spacingAndGlyphs">OPTIMALEN WETTKAMPF-</text>
        <text x="612" y="246" textLength="68" lengthAdjust="spacingAndGlyphs">VORBEREITUNG</text>
      </g>
    </g>
  </svg>

  <ul class="abs bullets bullets--problem">
    <li>Sie haben einen vollen Arbeitstag und wollen trotzdem endlich <em><i>Ihre Fitness verbessern</i></em>?</li>
    <li>Sie möchten dringend an <em><i>Ihrer Figur und Ihrem Gewicht</i></em> arbeiten?</li>
    <li>Sie wollen schon lange an Ihrem ersten <em><i>10 Kilometerlauf</i></em> teilnehmen und sich optimal darauf vorbereiten?</li>
    <li>Sie möchten einen Trainer haben, der Ihnen <em><i>jederzeit zur Verfügung</i></em> steht?</li>
    <li>Mit Ihrer Pulsuhr und Ihrer Lauf-App machen Sie nur geringe oder gar keine Trainingsfortschritte?</li>
  </ul>

  <ul class="abs bullets bullets--solution">
    <li>bietet Ihnen ein <em><i>optimales Lauftraining</i></em> im Freien durch eine kontrollierte, direkte Geschwindigkeitsvorgabe</li>
    <li>alarmiert Sie nicht nur wenn Sie etwas falsch machen <i>(indirektes Feedback)</i>, er <em><i>zeigt Ihnen wie Sie es richtig machen</i></em> <i>(direktes Feedback)</i></li>
    <li>führt dabei Trainingsprogramme aus, die auf <em><i>Ihre individuellen Fitness- und Leistungsziele</i></em> zugeschnitten sind</li>
    <li>verhindert, dass Sie sich beim <em><i>Training überlasten</i></em></li>
  </ul>

  <div class="abs availability">
    <p class="availability__title">KOBAL IST JEDERZEIT VERFÜGBAR.</p>
    <p class="availability__text">Sie müssen ihn nur einschalten, Ihr Trainingsprogramm auswählen und schon kann es losgehen!</p>
  </div>

  <ul class="abs howto">
    <li>• KOBAL ist ein elektrisch angetriebenes Fahrzeug</li>
    <li>• es fährt wie ein Tempomacher vor dem Läufer her</li>
    <li>• mit einer Geschwindigkeit, die so geregelt ist, dass ein bestimmter Puls erreicht und eingehalten werden kann. Ist Ihr Puls zu hoch wird KOBAL langsamer, ist Ihr Puls zu niedrig, beschleunigt KOBAL.</li>
    <li>• Er fährt selbständig und muss weder geschoben noch gelenkt werden. Sie laufen freihändig, wie Sie es gewohnt sind.</li>
    <li>• Er führt Programme aus, die Sie wie eine Smartphone App mit wenigen Mausklicks aus dem trabwerk Store herunterladen und installieren können.</li>
    <li>• Wie bei einem Laufband sind Sie mit KOBAL über eine Sicherungsleine verbunden. Wird diese Verbindung gelöst, bremst das Gerät sofort ab und bleibt stehen.</li>
  </ul>

  <address class="abs contact contact--address">Trabwerk GmbH<br>Lindenweg 22<br>D-80000 Musterstadt</address>
  <p class="abs contact contact--phone"><span class="contact__key">T</span> +49 000 123 456-0<br><span class="contact__key">F</span> +49 000 123 456-700</p>
  <p class="abs contact contact--web">info@trabwerk-beispiel.com<br>www.trabwerk-beispiel.com</p>
</section>

</body>
</html>
```